Covid 19 Exit Strategy one page brochure

I would like to design, and will need URGENT help, a brochure detailing a Covid 19 Exit Strategy plan. This brochure will need to be understood easily and the graphics inside should make it easy for people to understand without reading the entire text. This project is quite urgent and needs to be completed THIS WEEK - by Saturday may 16th at the latest. I am attaching two examples. I will provide the text.

```html
<!DOCTYPE html>
<html lang="en">
<head>
<meta charset="utf-8">
<title>Covid-19 Exit Strategy Brochure</title>
<link href="https://fonts.googleapis.com/css2?family=Poppins:wght@300;400;500;600;700&display=swap" rel="stylesheet">
<style>
:root{
  --teal:#12ab9b;
  --yellow:#ffe000;
  --pale-yellow:#faf6c8;
  --soft-yellow:#f3ee8a;
  --ink:#1b1b1b;
  --grey-logo:#9a9a9a;
  --stage:#7d7b8a;
  --white:#ffffff;
}
*{margin:0;padding:0;box-sizing:border-box}
html,body{width:1200px;height:2400px;overflow:hidden;background:var(--stage);font-family:'Poppins',sans-serif;color:var(--ink)}
.brochure{position:absolute;left:50px;top:489px;width:1100px;height:1422px;background:var(--white);box-shadow:0 4px 14px rgba(0,0,0,.25)}
.abs{position:absolute}
.brand{left:48px;top:89px;display:flex;align-items:center;gap:16px}
.brand-dot{width:112px;height:112px;border-radius:50%;background:var(--yellow)}
.brand-name{font-size:24px;font-weight:700;color:var(--grey-logo);letter-spacing:.5px}
.title{left:48px;top:240px;font-size:66px;font-weight:400;line-height:72px;letter-spacing:.5px}
.title-band{left:48px;top:416px;width:546px;height:54px;background:var(--teal);color:var(--white);font-size:30px;font-weight:500;line-height:54px;padding-left:24px;letter-spacing:.5px}
.hero-art{left:584px;top:47px;width:467px;height:495px}
.dash{left:484px;top:568px;width:94px;height:8px;background:var(--yellow)}
.section-title{left:0;width:100%;top:590px;text-align:center;font-size:54px;font-weight:700;color:var(--teal);letter-spacing:.5px}
.section-sub{left:0;width:100%;top:655px;text-align:center;font-size:33px;font-weight:500;letter-spacing:.3px}
.objective{left:233px;top:712px;font-size:19px;line-height:23px}
.objective .label{color:var(--teal)}
.objective .line2{padding-left:96px}
.step{position:absolute;width:323px;text-align:center;font-size:15.5px;line-height:17.5px}
.step.boxed{background:var(--pale-yellow);height:233px;top:788px}
.step .icon{width:106px;height:106px;border-radius:50%;background:var(--yellow);margin:13px auto 0}
.step.plain{top:1049px;height:200px}
.step.plain .icon{margin-top:0}
.step .hl{color:var(--teal);font-weight:700}
.step .copy{margin-top:28px}
.step.boxed .copy.low{margin-top:52px}
.step.plain .copy{margin-top:30px}
.step.plain .copy.low{margin-top:46px}
.divider{position:absolute;top:1059px;height:184px;border-left:2px dotted #555}
.footer-left{left:0;top:1271px;width:661px;height:106px;background:var(--teal);color:var(--white);padding:24px 0 0 45px}
.hashtag{font-size:38px;font-weight:700;line-height:40px}
.tagline{font-size:22px;font-weight:300;line-height:28px}
.footer-right{left:661px;top:1271px;width:439px;height:106px;background:var(--yellow)}
.more-info{left:40px;top:30px;font-size:20px;font-weight:700;line-height:24px}
.contact{left:206px;font-size:19px;display:flex;align-items:center;gap:8px}
.contact svg{width:18px;height:18px}
</style>
</head>
<body>
<main class="brochure">
  <div class="abs brand"><span class="brand-dot"></span><span class="brand-name">NORTHFIELD HEALTH</span></div>
  <h1 class="abs title">CORONAVIRUS<br>COVID–19</h1>
  <div class="abs title-band">INFORMATION AND GUIDELINES</div>

  <svg class="abs hero-art" viewBox="0 0 467 495" role="img" aria-label="Illustration of a group of office workers wearing face masks">
    <path d="M150 10 C230 -10 330 20 400 70 C470 130 470 260 440 340 C400 440 330 495 250 495 C160 495 70 440 40 340 C15 260 0 180 40 110 C70 60 100 25 150 10 Z" fill="var(--soft-yellow)"/>
    <circle cx="55" cy="95" r="55" fill="var(--yellow)"/>
    <path d="M40 230 C60 150 140 120 240 140 C340 150 410 200 430 280 C440 380 360 480 250 495 C150 495 60 430 40 330 Z" fill="#4a5fa8" opacity=".55"/>
  </svg>

  <div class="abs dash"></div>
  <h2 class="abs section-title">THE EXIT STRATEGY</h2>
  <p class="abs section-sub">WHAT DOES THE STRATEGY CONSIST OF?</p>
  <p class="abs objective"><span class="label">Objective:</span>&nbsp; To gradually phase out the restrictions imposed to curb<br><span class="line2">the spread of the coronavirus while remaining cautious.</span></p>

  <div class="step boxed" style="left:48px"><div class="icon" role="img" aria-label="Hospital building icon"></div><p class="copy low"><span class="hl">Ensure,</span><br>at all times, sufficient hospital<br>capacities.</p></div>
  <div class="step boxed" style="left:391px"><div class="icon" role="img" aria-label="Monitoring chart icon"></div><p class="copy"><span class="hl">Provide close monitoring</span><br>of &nbsp;the evolution of the pandemic<br>during the entire exit, as well as the<br>secondary effects of the<br>confinement.</p></div>
  <div class="step boxed" style="left:736px"><div class="icon" role="img" aria-label="Distancing people icon"></div><p class="copy"><span class="hl">Apply basic barrier gestures</span><br>and reinforce them with other ' fill<br>specific measures, including in the<br>workplace, to minimize the risk of an<br>uncontrolled spread of the virus.</p></div>

  <div class="step plain" style="left:48px"><div class="icon" role="img" aria-label="Crowd and globe icon"></div><p class="copy">Foresee the possibility of reintroducing<br><span class="hl">stricter measures</span> in the event of a<br>strong resurgence of the virus among<br>the population.</p></div>
  <div class="divider" style="left:382px"></div>
  <div class="step plain" style="left:391px"><div class="icon" role="img" aria-label="Test tube and magnifier icon"></div><p class="copy"><span class="hl">Foster testing capacities</span><br>and &nbsp;support research in particular with<br>regard to tests to measure the acquired<br>immunity of the population.</p></div>
  <div class="divider" style="left:726px"></div>
  <div class="step plain" style="left:736px"><div class="icon" role="img" aria-label="Protective shield icon"></div><p class="copy low"><span class="hl">Protect,</span><br>in particular, vulnerable groups.</p></div>

  <footer>
    <div class="abs footer-left">
      <p class="hashtag">#BLEIFTDOHEEM</p>
      <p class="tagline">DON'T HAVE TO GO OUTSIDE? PLEASE STAY AT HOME!</p>
    </div>
    <div class="abs footer-right">
      <p class="abs more-info">FOR MORE<br>INFORMATION</p>
      <p class="abs contact" style="top:22px">
        <svg viewBox="0 0 20 20"><circle cx="10" cy="10" r="8.5" fill="none" stroke="var(--teal)" stroke-width="2"/><ellipse cx="10" cy="10" rx="3.5" ry="8.5" fill="none" stroke="var(--teal)" stroke-width="1.6"/><path d="M2 10h16" stroke="var(--teal)" stroke-width="1.6"/></svg>
        www.exitplaninfo.org</p>
      <p class="abs contact" style="top:54px">
        <svg viewBox="0 0 20 20"><path d="M4 2l4 1 1 4-2 2c1 2 3 4 5 5l2-2 4 1 1 4-2 2C9 19 1 11 2 4z" fill="var(--teal)"/></svg>
        555-014-2290</p>
    </div>
  </footer>
</main>
</body>
</html>
```